Business card design for my company.
I would like the card's background colour to be black. You can also see our web site to get an idea of our brand. https://www.tmwhomecrafting.com.au/
- Name
- Email

```html
<!DOCTYPE html>
<html lang="en">
<head>
<meta charset="utf-8">
<title>TMW Home Crafting – Business Card</title>
<link href="https://fonts.googleapis.com/css2?family=Poppins:wght@400;500;700&display=swap" rel="stylesheet">
<style>
  :root {
    --backdrop: #8c8c8c;
    --card-dark: #1e1e1e;
    --brand-green: #0a9444;
    --white: #ffffff;
    --logo-grey: #9a9a9a;
  }
  * { margin: 0; padding: 0; box-sizing: border-box; }
  html, body {
    width: 1200px; height: 1122px; overflow: hidden;
    background: var(--backdrop);
    font-family: "Poppins", sans-serif;
  }
  .sheet { position: relative; width: 1200px; height: 1122px; }
  .card {
    position: absolute; left: 160px; width: 880px; height: 503px;
    border-radius: 30px; overflow: hidden; background: var(--card-dark);
  }
  .card--back { top: 40px; }
  .card--front { top: 579px; background: var(--brand-green); }

  .wordmark {
    position: absolute; display: flex; align-items: center; gap: 14px;
    font-weight: 700; letter-spacing: 4px; text-transform: uppercase;
  }
  .wordmark__square { width: 22px; height: 22px; }
  .card--back .wordmark {
    left: 0; right: 0; top: 225px; justify-content: center;
    font-size: 40px; color: var(--logo-grey);
  }
  .card--back .wordmark__square { background: var(--brand-green); }

  .front-shape { position: absolute; inset: 0; }
  .card--front .wordmark {
    left: 530px; width: 330px; top: 190px; justify-content: center;
    font-size: 26px; color: var(--white); letter-spacing: 2px;
    flex-wrap: wrap; text-align: center; line-height: 1.25;
  }
  .card--front .wordmark__square { background: var(--brand-green); }

  .identity { position: absolute; left: 62px; top: 200px; color: var(--white); }
  .identity__name { font-size: 36px; font-weight: 700; letter-spacing: 1px; text-transform: uppercase; line-height: 1.1; }
  .identity__role { font-size: 21px; font-weight: 500; margin-top: 2px; }

  .contacts { position: absolute; left: 72px; top: 330px; list-style: none; color: var(--white); }
  .contacts li { display: flex; align-items: center; gap: 12px; font-size: 19px; font-weight: 500; height: 33px; }
  .contacts svg { width: 18px; height: 18px; flex: none; }
</style>
</head>
<body>
<main class="sheet">
  <section class="card card--back" aria-label="Card back">
    <div class="wordmark"><span class="wordmark__square"></span>TMW Home Crafting</div>
  </section>

  <section class="card card--front" aria-label="Card front">
    <svg class="front-shape" viewBox="0 0 880 503" aria-hidden="true">
      <polygon points="548,0 880,0 880,503 812,503 472,300" fill="var(--card-dark)"/>
      <polyline points="538,0 462,302 800,503" fill="none" stroke="var(--card-dark)" stroke-width="20"/>
      <polyline points="544,0 468,302 806,503" fill="none" stroke="var(--white)" stroke-width="10"/>
      <line x1="532" y1="40" x2="500" y2="170" stroke="var(--brand-green)" stroke-width="3"/>
      <line x1="540" y1="352" x2="770" y2="488" stroke="var(--brand-green)" stroke-width="3"/>
    </svg>

    <div class="wordmark"><span class="wordmark__square"></span>TMW Home Crafting</div>

    <div class="identity">
      <h1 class="identity__name">Liam Carver</h1>
      <p class="identity__role">General Manager</p>
    </div>

    <ul class="contacts">
      <li>
        <svg viewBox="0 0 24 24" fill="var(--white)"><path d="M6.6 10.8a15 15 0 0 0 6.6 6.6l2.2-2.2a1 1 0 0 1 1-.25 11.4 11.4 0 0 0 3.6.57 1 1 0 0 1 1 1V20a1 1 0 0 1-1 1A17 17 0 0 1 3 4a1 1 0 0 1 1-1h3.5a1 1 0 0 1 1 1c0 1.25.2 2.45.57 3.57a1 1 0 0 1-.25 1z"/></svg>
        0400 123 456
      </li>
      <li>
        <svg viewBox="0 0 24 24" fill="none" stroke="var(--white)" stroke-width="2"><rect x="3" y="5" width="18" height="14" rx="1"/><path d="M3 6l9 7 9-7"/></svg>
        info@tmwhomecrafting.com.au
      </li>
      <li>
        <svg viewBox="0 0 24 24" fill="none" stroke="var(--white)" stroke-width="2"><circle cx="12" cy="12" r="9"/><path d="M3 12h18M12 3c3 3 3 15 0 18M12 3c-3 3-3 15 0 18"/></svg>
        tmwhomecrafting.com.au
      </li>
      <li>
        <svg viewBox="0 0 24 24" fill="var(--white)"><path d="M12 2a7 7 0 0 0-7 7c0 5 7 13 7 13s7-8 7-13a7 7 0 0 0-7-7zm0 9.5A2.5 2.5 0 1 1 12 6.5a2.5 2.5 0 0 1 0 5z"/></svg>
        Devonport, Tasmania, Australia
      </li>
    </ul>
  </section>
</main>
</body>
</html>
```